Coastal Learner Bureau business cards

Australian company about to start offering its services. We recruit international students to come to study English, vocational education and postgraduate courses in Australia. We help them find the institution and select the right city they want to come to Australia. We are a young, online oriented and supportive agency. Our clients are between 18 and 35 years old, mainly University students, young professionals or people with work experience. We provide much more information that any other agency offer. We administrate a Facebook group with more than 11.000 members that daily ask questions about general information when coming to Australia, while they are here and even after they leave the country

Target Market(s)

International students from South America, Central America and Europe

Industry/Entity Type

Student

Contact Information for Business Card

Tomas Bilbrea
Managing Director
tomas@kelvarin.com.au
www.kelvoria.com.au
+61 491058264
Melbourne, Australia

Font styles to use
Serif
Sans Serif

Colors

Designer to choose colors to be used in the design.

Requirements
Must have
• Horizontal design
• Standard business card size and shape. If font uses green or yellow colours, they will have to match the ones from the logo
Nice to have
• UPDATE: Use the contents of the green image to design one of the card sides. Use our logo in the background of that side as watermark.
• Passport image, or immigration stamps. A picture of the Yarra River (from Melbourne) would be cool as well.
Should not have
• Non-standard business card size and shape
• Not black as the background colour of any sides as we are not a VIP agency or a hight class service. We are orientes to young people and they like colours, pictures, something attractive.
• Vertical design
• NO YELLOW or BLACK AS THE BACKGROUND COLOUR OF ANY SIDE OF THE BIZ CARD

```html
<!DOCTYPE html>
<html lang="en">
<head>
<meta charset="utf-8">
<title>Coastal Learner Bureau business cards</title>
<link rel="stylesheet" href="https://fonts.googleapis.com/css2?family=Source+Sans+3:wght@400;600;700&display=swap">
<style>
  :root {
    --backdrop: #000000;
    --card: #2e2e30;
    --brand-green: #1f7a3c;
    --brand-yellow: #e8b818;
    --text-light: #e6e6e6;
    --text-white: #ffffff;
    --divider: #47474a;
  }
  * { margin: 0; padding: 0; box-sizing: border-box; }
  html, body {
    width: 1200px; height: 899px; overflow: hidden;
    background: var(--backdrop);
    font-family: "Source Sans 3", sans-serif;
  }
  .stage { position: relative; width: 1200px; height: 899px; }
  .card {
    position: absolute; top: 270px; width: 456px; height: 281px;
    background: var(--card); border-radius: 13px;
  }
  .card--front { left: 137px; }
  .card--back { left: 627px; }

  .brand {
    position: absolute; display: flex; align-items: center; gap: 8px;
    color: var(--brand-green); font-weight: 700; font-size: 30px; letter-spacing: 0.2px;
  }
  .brand__dot {
    width: 14px; height: 14px; border-radius: 50%; background: var(--brand-yellow);
  }
  .card--front .brand { left: 40px; top: 122px; }
  .card--back .brand { left: 40px; top: 122px; }

  .divider {
    position: absolute; left: 231px; top: 86px; width: 1px; height: 124px;
    background: var(--divider);
  }
  .contact { position: absolute; left: 259px; top: 70px; color: var(--text-light); }
  .contact__name {
    color: var(--brand-yellow); font-weight: 600; font-size: 16.5px; line-height: 20px;
  }
  .contact__role { font-size: 12.5px; line-height: 16px; }
  .contact__city { font-size: 12.5px; line-height: 16px; margin-top: 17px; }
  .contact__list { list-style: none; margin-top: 13px; }
  .contact__item {
    display: flex; align-items: center; gap: 6px;
    font-size: 12.5px; line-height: 19px;
  }
  .contact__icon { width: 9px; height: 9px; fill: var(--brand-yellow); flex: none; }

  .slogan {
    position: absolute; left: 255px; top: 54px;
    color: var(--text-white); font-weight: 600; line-height: 1; text-transform: uppercase;
  }
  .slogan__lead { display: block; font-size: 31px; letter-spacing: 0.5px; }
  .slogan__big { display: block; font-size: 74px; font-weight: 700; margin-top: 4px; letter-spacing: 1px; }
  .slogan__tail { display: block; font-size: 40px; margin-top: 4px; }
</style>
</head>
<body>
<main class="stage">
  <section class="card card--front" aria-label="Business card front">
    <div class="brand"><span class="brand__name">Kelvoria</span><span class="brand__dot"></span></div>
    <div class="divider"></div>
    <div class="contact">
      <p class="contact__name">Tomas Bilbrea</p>
      <p class="contact__role">Managing Director</p>
      <p class="contact__city">Melbourne, Australia</p>
      <ul class="contact__list">
        <li class="contact__item">
          <svg class="contact__icon" viewBox="0 0 10 10"><path d="M2 0.5 L3.6 2.8 L2.7 3.8 Q3.7 5.9 6.2 7.3 L7.2 6.4 L9.5 8 L8.4 9.5 Q4.5 9.4 1.8 6.3 Q0.2 4 0.6 1.6 Z"/></svg>
          +61 491058264
        </li>
        <li class="contact__item">
          <svg class="contact__icon" viewBox="0 0 10 10"><path d="M0.5 2 H9.5 V8.5 H0.5 Z M0.5 2 L5 5.5 L9.5 2" stroke="#2e2e30" stroke-width="0.8"/></svg>
          tomas@kelvarin.com.au
        </li>
        <li class="contact__item">
          <svg class="contact__icon" viewBox="0 0 10 10"><circle cx="5" cy="5" r="4.6"/></svg>
          www.kelvoria.com.au
        </li>
      </ul>
    </div>
  </section>

  <section class="card card--back" aria-label="Business card back">
    <div class="brand"><span class="brand__name">Kelvoria</span><span class="brand__dot"></span></div>
    <h2 class="slogan">
      <span class="slogan__lead">Hacemos</span>
      <span class="slogan__big">Más</span>
      <span class="slogan__tail">Por ti !</span>
    </h2>
  </section>
</main>
</body>
</html>
```